The most modern business card ever !!!

Our company call “Vendalo”. Vendalo is a technology company specialized in cruises solutions. Out main product is a platform to reserve cruises. This is a revolutionary platform that make easier to travel agencies and final users to reserve cruises across dozen companies like tibba, wernu, hpv, dgb, etc..We are a “start up”, with a young team of developers and we want to transmit it.. For it, we want something different, a modern business card that represent cruises and technology.. When someone receive this card, this person should say: wowww this is different… this is modern… this is a cruise related company..
- diferent, modern
- traditions business card

```html
<!DOCTYPE html>
<html lang="en">
<head>
<meta charset="UTF-8">
<title>Vendalo Business Card</title>
<link href="https://fonts.googleapis.com/css2?family=Lato:wght@400;700&display=swap" rel="stylesheet">
<style>
  :root {
    --backdrop: #c8c8c8;
    --brand-blue: #29a8e0;
    --card-white: #f4f5f4;
    --ink: #111111;
    --ink-soft: #333333;
    --radius: 22px;
  }
  html, body {
    margin: 0;
    padding: 0;
    width: 1200px;
    height: 1200px;
    overflow: hidden;
    background: var(--backdrop);
    font-family: "Lato", sans-serif;
  }
  .canvas {
    position: relative;
    width: 1200px;
    height: 1200px;
  }
  .card {
    position: absolute;
    left: 251px;
    width: 706px;
    height: 403px;
    border-radius: var(--radius);
    box-sizing: border-box;
  }
  .card--front {
    top: 144px;
    background: var(--brand-blue);
    display: flex;
    align-items: center;
    justify-content: center;
  }
  .card--back {
    top: 583px;
    background: var(--card-white);
  }
  .wordmark {
    font-weight: 700;
    letter-spacing: 2px;
    line-height: 1;
  }
  .card--front .wordmark {
    color: #ffffff;
    font-size: 104px;
  }
  .card--back .wordmark {
    position: absolute;
    left: 66px;
    top: 154px;
    color: var(--ink);
    font-size: 64px;
  }
  .divider {
    position: absolute;
    left: 381px;
    top: 107px;
    width: 2px;
    height: 188px;
    background: var(--brand-blue);
  }
  .details {
    position: absolute;
    left: 407px;
    top: 101px;
    color: var(--ink-soft);
    font-size: 17px;
    line-height: 23px;
  }
  .details p { margin: 0; }
  .person-name {
    font-size: 22px;
    font-weight: 700;
    color: var(--ink);
    line-height: 26px;
  }
  .person-role { margin-bottom: 19px !important; }
  .address { margin-bottom: 15px !important; }
  .web-accent { color: var(--brand-blue); }
</style>
</head>
<body>
  <main class="canvas">
    <section class="card card--front">
      <span class="wordmark">Vendalo</span>
    </section>

    <section class="card card--back">
      <span class="wordmark">Vendalo</span>
      <div class="divider"></div>
      <div class="details">
        <p class="person-name">Dario Mendes</p>
        <p class="person-role">Director</p>
        <div class="address">
          <p>48/3 Harbour Lane</p>
          <p>Wellmoor,TS.500218-QRA</p>
        </div>
        <div class="contact">
          <p>+244 555 019</p>
          <p>info@vendalo.com</p>
          <p>www.<span class="web-accent">vendalo</span>.com</p>
        </div>
      </div>
    </section>
  </main>
</body>
</html>
```